Tovimar Community Development Planning New web site

Design a new web site. I have a budget of $1,500.00.
Attached on PowerPoint is a complete site plan. Home page and linked pages.
10 - 12 pages. All copy and photos will be supplied. (300dpi)
I have shown them the concept which they like.
No data bases required. Home page with animations dissolving.
They former web site has been taken down. They have been in business 30 years in New Jersey
Colors teal blues and greens
There will be a new logo)being designed)
The text in home page copy will give you a detailed story what they are all about.

files have been approved for Tovimar, Inc.   Brenton is the designer

```html
<!DOCTYPE html>
<html lang="en">
<head>
<meta charset="utf-8">
<title>Tovimar, Inc. — Community Development Planning</title>
<link rel="stylesheet" href="https://fonts.googleapis.com/css2?family=Open+Sans:wght@300;400;600&family=Tinos:wght@400;700&display=swap">
<style>
:root{
  --ink:#222;
  --text:#555;
  --muted:#7a7a7a;
  --blue:#1f5fa6;
  --blue-dark:#164a8a;
  --teal-top:#2fa9b6;
  --teal-bottom:#117d8a;
  --green:#6aa621;
  --green-dark:#5a9118;
  --rule:#dedede;
  --band:#f1f1f1;
  --footer:#f6f6f6;
}
*{margin:0;padding:0;box-sizing:border-box}
html,body{width:1200px;height:1187px;overflow:hidden;background:#fff}
body{position:relative;font-family:"Open Sans",Arial,sans-serif;color:var(--text)}
.top-rule{position:absolute;left:0;top:0;width:1200px;height:5px;background:#ddd}
.hero-band{position:absolute;left:0;top:172px;width:1200px;height:208px;background:linear-gradient(#fff,var(--band))}

.brand{position:absolute;left:110px;top:40px;font-family:"Tinos",serif;color:#111}
.brand-name{font-size:33px;line-height:36px}
.brand-tag{font-size:16.5px;font-weight:700;letter-spacing:-.3px;margin-top:2px}

.contact{position:absolute;right:112px;top:54px;text-align:right}
.contact-phone{font-size:29px;color:var(--blue);line-height:34px}
.contact-email{font-size:12.5px;color:var(--blue);margin-top:2px}

.main-nav{position:absolute;left:107px;top:120px;width:986px;height:52px;display:flex;
  background:linear-gradient(var(--teal-top),var(--teal-bottom))}
.main-nav a{display:flex;align-items:center;justify-content:center;color:#fff;text-decoration:none;
  font-size:14.5px;text-transform:uppercase;border-right:1px solid rgba(0,0,0,.15);
  box-shadow:inset -1px 0 0 rgba(255,255,255,.12)}
.main-nav a:last-child{border-right:none;box-shadow:none}

.slider{position:absolute;left:107px;top:172px;width:986px;height:370px;background:#fff;border:1px solid #ddd;border-top:none}
.slide-photo{position:absolute;left:137px;top:0;width:700px;height:369px;
  background:radial-gradient(ellipse at 50% 55%,#c98d6e 0%,#a8744f 35%,#6b8fb4 70%,#f2f2f2 100%)}
.slider-arrow{position:absolute;top:140px}
.slider-arrow.prev{left:20px}
.slider-arrow.next{right:14px}

.intro{position:absolute;left:107px;top:564px;width:986px;text-align:center}
.intro h1{font-weight:400;font-size:30px;color:#333;line-height:40px}
.intro p{font-size:13px;line-height:21px;color:var(--muted);margin-top:3px}
.divider{position:absolute;left:107px;top:680px;width:986px;height:1px;background:var(--rule)}

.about{position:absolute;left:107px;top:710px;width:472px}
.about h2,.results h2{font-weight:400;font-size:27px;line-height:36px}
.about h2{color:var(--blue)}
.about p{font-size:12.4px;line-height:21px;margin-top:10px;color:var(--text)}
.about p + p{margin-top:9px}

.btn{position:absolute;top:990px;width:101px;height:30px;border-radius:3px;color:#fff;
  font-size:11.5px;font-weight:600;text-transform:uppercase;display:flex;align-items:center;justify-content:center;text-decoration:none}
.btn-blue{left:107px;background:linear-gradient(#2869b3,var(--blue-dark))}
.btn-green{left:635px;background:linear-gradient(#79b82c,var(--green-dark))}

.results{position:absolute;left:626px;top:710px;width:466px}
.results h2{color:var(--green)}
.results ul{list-style:none;margin:8px 0 0 8px}
.results li{position:relative;padding:6px 0 6px 23px;font-size:13px;line-height:21px;border-bottom:1px solid var(--rule)}
.results li:last-child{border-bottom:none}
.results li svg{position:absolute;left:0;top:10px}

.site-footer{position:absolute;left:0;top:1076px;width:1200px;height:111px;background:var(--footer);border-top:1px solid #e4e4e4}
.footer-links{position:absolute;left:107px;top:28px;font-size:15px;color:#444}
.footer-links span{margin:0 9px;color:#555}
.copyright{position:absolute;left:107px;top:62px;font-size:12.5px;color:var(--muted)}
.social{position:absolute;top:27px;width:24px;height:24px;border-radius:2px}
.social.s1{left:992px;background:#3b5b99}
.social.s2{left:1026px;background:#55b7e8}
.social.s3{left:1058px;background:#1f78b8}
</style>
</head>
<body>
<div class="top-rule"></div>
<div class="hero-band"></div>

<header>
  <div class="brand">
    <div class="brand-name">Tovimar, Inc.</div>
    <div class="brand-tag">Community Development Planning</div>
  </div>
  <div class="contact">
    <div class="contact-phone">(555) 014-2298</div>
    <div class="contact-email">tovimar@ mailnet.com</div>
  </div>
</header>

<nav class="main-nav">
  <a href="#" style="width:96px">Home</a>
  <a href="#" style="width:146px">Our Company</a>
  <a href="#" style="width:106px">Services</a>
  <a href="#" style="width:258px">Housing Rehab Application</a>
  <a href="#" style="width:232px">Affordable Application</a>
  <a href="#" style="width:148px">Contact Us</a>
</nav>

<section class="slider">
  <div class="slide-photo" role="img" aria-label="Group photo of a diverse crowd of community residents smiling"></div>
  <svg class="slider-arrow prev" width="26" height="70" viewBox="0 0 26 70"><polyline points="25,1 2,35 25,69" fill="none" stroke="#999" stroke-width="1.5"/></svg>
  <svg class="slider-arrow next" width="26" height="70" viewBox="0 0 26 70"><polyline points="1,1 24,35 1,69" fill="none" stroke="#999" stroke-width="1.5"/></svg>
</section>

<section class="intro">
  <h1>Mauris vel lacus vitae felis vestibulum volutpat</h1>
  <p>Curabitur tristique mi condimentum orci Phasellus pellentesque aliquam enim Proin dui lectus cursus eu mattis laoreet viverra sit amet quam<br>Curabitur vel dolor ultrices ipsum dictum tristique Praesent vitae lacus Ut velit enim vestibulum non fermentum nec hendrerit</p>
</section>
<div class="divider"></div>

<section class="about">
  <h2>About Our Company</h2>
  <p>Tovimar, Inc. is a city planning firm that specializes in community development and housing rehabilitation program planning, design and implementation. We have over twenty years of experience in developing and administering income base-base housing and programs in accordance with US Department of Housing and Urban Development (HUD) and New Jersey Council on Affordable Housing (COAH) rules and regulations,</p>
  <p>&nbsp;In addition, our firm is capable of providing the technical and administrative assistance our clients require for implementation of their income based housing programs. Harwell Linden Associates is one of the most experience urban planning firms in New Jersey, with over forty years of as consulting planners.</p>
</section>
<a class="btn btn-blue" href="#">Read More</a>

<section class="results">
  <h2>We Get Results</h2>
  <ul>
    <li><svg width="17" height="13" viewBox="0 0 17 13"><path d="M1 7 L6 12 L16 1" fill="none" stroke="#6aa621" stroke-width="3"/></svg>Tovimar designs income based programs to be supported by federal placement lotteries state funding.</li>
    <li><svg width="17" height="13" viewBox="0 0 17 13"><path d="M1 7 L6 12 L16 1" fill="none" stroke="#6aa621" stroke-width="3"/></svg>We implement local programs to benefit people seeking access to affordable housing</li>
    <li><svg width="17" height="13" viewBox="0 0 17 13"><path d="M1 7 L6 12 L16 1" fill="none" stroke="#6aa621" stroke-width="3"/></svg>Our experienced staff screen applicants for local affordable housing</li>
    <li><svg width="17" height="13" viewBox="0 0 17 13"><path d="M1 7 L6 12 L16 1" fill="none" stroke="#6aa621" stroke-width="3"/></svg>We pre-qualify persons who have applied for housing rehabilitation</li>
    <li><svg width="17" height="13" viewBox="0 0 17 13"><path d="M1 7 L6 12 L16 1" fill="none" stroke="#6aa621" stroke-width="3"/></svg>Conduct placement lotteries</li>
  </ul>
</section>
<a class="btn btn-green" href="#">View More</a>

<footer class="site-footer">
  <div class="footer-links">Home<span>|</span>Our Company<span>|</span>Services<span>|</span>Housing Rehab Application<span>|</span>Affordable Application<span>|</span>Contact Us</div>
  <div class="copyright">Copy Right 2014 Tovimar, 112 Harborline Road, Eastfield, New Jersey, 08999</div>
  <div class="social s1"></div>
  <div class="social s2"></div>
  <div class="social s3"></div>
</footer>
</body>
</html>
```